Birchpoint Studio Complementary Pass

I’d like a complimentary pass for any 30-minute Birchpoint Studio session. Choose one of the following options: Infrared Sauna with Red Light, Massage Chair Veltrafix Compression Therapy, or Paraffin Wax Hand Bath.

Please incorporate the logo and brand colors into your design. I’d like a square image that will be printed on square business cards (no rectangles).

Please refer to the logo and menu for more details.

Contact Information for Business Card

See discretion

```html
<!DOCTYPE html>
<html lang="en">
<head>
<meta charset="utf-8">
<title>Birchpoint Studio Complimentary Pass</title>
<link href="https://fonts.googleapis.com/css2?family=Montserrat:wght@400;500;600&family=Oswald:wght@400&family=Cormorant+Garamond:wght@500&family=Dancing+Script:wght@500&display=swap" rel="stylesheet">
<style>
  :root{
    --backdrop:#b5b5b5;
    --coral:#f26b4f;
    --coral-deep:#c9302c;
    --purple:#46318f;
    --purple-soft:#5a47ad;
    --ink:#2d2a7c;
    --white:#ffffff;
  }
  *{margin:0;padding:0;box-sizing:border-box}
  html,body{width:1200px;height:960px;overflow:hidden;background:var(--backdrop)}
  body{position:relative;font-family:"Montserrat",sans-serif}
  .card{position:absolute;top:281px;width:400px;height:400px;border-radius:20px;overflow:hidden}
  .card--front{left:166px;background:var(--coral)}
  .card--back{left:635px;background:var(--white);color:var(--ink)}

  .front-pattern{position:absolute;inset:0;
    background:linear-gradient(160deg,#f27a5e 0%,var(--coral) 45%,#e0483a 75%,var(--coral-deep) 100%)}
  .front-brand{position:absolute;left:0;right:0;top:205px;text-align:center;
    font-weight:500;font-size:64px;color:var(--purple);letter-spacing:-1px;line-height:1}
  .front-tagline{position:absolute;left:0;right:0;top:290px;text-align:center;
    font-family:"Oswald",sans-serif;font-size:23px;letter-spacing:3px;color:var(--purple-soft)}

  .back-brand{position:absolute;left:0;right:0;top:38px;text-align:center;
    font-weight:500;font-size:20px;color:var(--purple);line-height:1}
  .back-tagline{position:absolute;left:0;right:0;top:65px;text-align:center;
    font-size:5.5px;letter-spacing:.6px;font-weight:600;color:var(--purple)}
  .pass-title{position:absolute;left:0;right:0;top:76px;text-align:center;
    font-family:"Cormorant Garamond",serif;font-size:41px;color:var(--ink);line-height:1}
  .pass-script{position:absolute;left:172px;top:106px;
    font-family:"Dancing Script",cursive;font-size:22px;color:var(--ink);line-height:1}
  .entitles{position:absolute;left:0;right:0;top:140px;text-align:center;font-size:11px}
  .offer{position:absolute;left:0;right:0;top:156px;text-align:center;
    font-weight:600;font-size:15.5px;line-height:17px;color:var(--ink)}
  .offer em{font-style:normal;color:var(--coral)}
  .choose{position:absolute;left:35px;top:196px;font-size:10px;font-weight:500;color:var(--coral)}
  .choose-line{position:absolute;left:230px;top:207px;width:112px;height:1px;background:var(--ink)}
  .options{position:absolute;left:35px;top:214px;list-style:none}
  .options li{display:flex;align-items:center;gap:8px;height:25.3px;font-size:10.5px}
  .tick{width:12px;height:12px;flex:none}
  .terms{position:absolute;left:0;right:0;bottom:0;height:89px;background:var(--purple);color:var(--white)}
  .terms-title{position:absolute;left:0;right:0;top:5px;text-align:center;
    font-size:10px;font-weight:500;color:var(--coral)}
  .term{position:absolute;top:29px;font-size:10.5px;line-height:13px}
  .term .tick{display:block;margin-bottom:2px}
  .term--one{left:28px;text-align:center}
  .term--one .tick{margin-left:24px}
  .term--two{left:144px}
  .term--two .tick{margin-left:30px}
  .term--three{left:302px}
  .term--three .tick{margin-left:35px}
</style>
</head>
<body>
  <section class="card card--front">
    <div class="front-pattern" role="img" aria-label="Repeating brand pattern in coral and deep red tones"></div>
    <div class="front-brand">halvera</div>
    <div class="front-tagline">PHYSICAL THERAPY</div>
  </section>

  <section class="card card--back">
    <div class="back-brand">halvera</div>
    <div class="back-tagline">PHYSICAL THERAPY</div>
    <div class="pass-title">complimentary</div>
    <div class="pass-script">pass</div>
    <p class="entitles">This card entitles you to</p>
    <p class="offer">ANY ONE <em>30-MIUTE</em><br>BIRCHPOINT STUDIO SESSION</p>
    <p class="choose">CHOSSE ONE OF THE FOLLOWING:</p>
    <div class="choose-line"></div>
    <ul class="options">
      <li><svg class="tick" viewBox="0 0 12 12"><circle cx="6" cy="6.5" r="4.8" fill="none" stroke="#f26b4f" stroke-width="1.1"/><path d="M3.6 6.4l2 2L10.5 1.5" fill="none" stroke="#f26b4f" stroke-width="1.2"/></svg>Infrared Sauna + Red Light</li>
      <li><svg class="tick" viewBox="0 0 12 12"><circle cx="6" cy="6.5" r="4.8" fill="none" stroke="#f26b4f" stroke-width="1.1"/><path d="M3.6 6.4l2 2L10.5 1.5" fill="none" stroke="#f26b4f" stroke-width="1.2"/></svg>Massage Chair</li>
      <li><svg class="tick" viewBox="0 0 12 12"><circle cx="6" cy="6.5" r="4.8" fill="none" stroke="#f26b4f" stroke-width="1.1"/><path d="M3.6 6.4l2 2L10.5 1.5" fill="none" stroke="#f26b4f" stroke-width="1.2"/></svg>Veltrafix Compression Therapy</li>
      <li><svg class="tick" viewBox="0 0 12 12"><circle cx="6" cy="6.5" r="4.8" fill="none" stroke="#f26b4f" stroke-width="1.1"/><path d="M3.6 6.4l2 2L10.5 1.5" fill="none" stroke="#f26b4f" stroke-width="1.2"/></svg>Paraffin Wax Hand Bath</li>
    </ul>
    <div class="terms">
      <p class="terms-title">TERMS &amp; CONDITIONS</p>
      <div class="term term--one"><svg class="tick" viewBox="0 0 12 12"><circle cx="6" cy="6.5" r="4.8" fill="none" stroke="#f26b4f" stroke-width="1.1"/><path d="M3.6 6.4l2 2L10.5 1.5" fill="none" stroke="#f26b4f" stroke-width="1.2"/></svg>One-time<br>use only</div>
      <div class="term term--two"><svg class="tick" viewBox="0 0 12 12"><circle cx="6" cy="6.5" r="4.8" fill="none" stroke="#f26b4f" stroke-width="1.1"/><path d="M3.6 6.4l2 2L10.5 1.5" fill="none" stroke="#f26b4f" stroke-width="1.2"/></svg>Not redeeable<br>for cash</div>
      <div class="term term--three"><svg class="tick" viewBox="0 0 12 12"><circle cx="6" cy="6.5" r="4.8" fill="none" stroke="#f26b4f" stroke-width="1.1"/><path d="M3.6 6.4l2 2L10.5 1.5" fill="none" stroke="#f26b4f" stroke-width="1.2"/></svg>Must present<br>this card at<br>time of visit</div>
    </div>
  </section>
</body>
</html>
```